Economics of an Assumption vs Obtaining a New Loan at Current Market Rate

I need to marketing flyer that has fields that calculate mortgage payments amongst other calculations. I have a rough draft that I will attach.

The idea is to provide a tool for a real estate agent to use to illustrate to a potential buyer what a payment would be if they assumed the existing loan on the house or took out a new loan at current market.

The flyer needs to be able to allow an agent to drop in their logo, photo, and contact along with the loan officers photo and contact info.

You can google open house flyer to see examples of what the overall artwork and presentation can look like.

Target Market(s)

Home Buyers

Industry/Entity Type

Real Estate

Colors
F0912C
F2A743
F7CA91
FBE8D2
FDF5EE
EE7325
F08F49
F5BC92
FAE3D3
FDF4ED

Requirements
Must have
• A way to calculate mortgage payment
Nice to have
• Photo and logo drop ins

```html
<!DOCTYPE html>
<html lang="en">
<head>
<meta charset="utf-8">
<title>Assumption vs New Loan – Keyvale</title>
<link href="https://fonts.googleapis.com/css2?family=Open+Sans:wght@700;800&family=Source+Sans+3:ital,wght@0,400;0,600;0,700;1,400&display=swap" rel="stylesheet">
<style>
:root{
  --orange:#F0912C;
  --orange-deep:#EE7325;
  --orange-soft:#F7CA91;
  --cream:#FDF5EE;
  --ink:#111111;
  --white:#ffffff;
}
*{box-sizing:border-box;margin:0;padding:0}
html,body{width:856px;height:1200px;overflow:hidden;background:#fff}
body{font-family:"Source Sans 3",Arial,sans-serif;color:var(--ink)}
.flyer{position:relative;width:856px;height:1200px;background:#fbfbfb;overflow:hidden}
.abs{position:absolute}
.hero-photo{left:0;top:0;width:856px;height:470px;
  background:linear-gradient(180deg,#5a6fa0 0%,#8d8fb0 20%,#b9a08a 38%,#b8895e 55%,#a47a52 72%,#8a8078 84%,#a9a29a 100%)}
.header-swoosh,.hero-curve{left:0;top:0}
.brand{display:flex;align-items:center;gap:6px;font-family:"Source Sans 3",Arial,sans-serif;font-weight:400;color:var(--orange-deep);white-space:nowrap}
.brand-mark{width:30px;height:30px;border-radius:50%;background:var(--orange-deep);flex:none}
.brand-top{left:108px;top:46px;font-size:44px}
.purchase-label{left:158px;top:508px;font-weight:700;font-size:36px;letter-spacing:.5px}
.purchase-box{left:480px;top:511px;width:220px;height:41px;border:2px solid #222;border-radius:4px;background:#fff}
.section-band{height:42px;display:flex;align-items:center;font-family:"Open Sans",Arial,sans-serif;font-weight:800;font-size:21px;letter-spacing:1.3px;border-radius:0 21px 21px 0;white-space:nowrap}
.band-current{left:12px;top:572px;width:295px;padding-left:14px;background:linear-gradient(90deg,var(--orange) 0%,var(--orange-soft) 55%,var(--cream) 100%)}
.band-new{left:399px;top:572px;width:433px;padding-left:13px;letter-spacing:1px;background:linear-gradient(90deg,var(--orange) 0%,var(--orange-soft) 45%,var(--cream) 100%)}
.label{font-size:18.5px;font-weight:600;line-height:1;white-space:nowrap}
.colon{font-size:18px;font-weight:600}
.field{height:22px;border:1.5px solid #222;background:#fff;font-size:12.5px;display:flex;align-items:center;padding-left:20px;white-space:nowrap}
.field.center{justify-content:center;padding-left:0}
.field small{font-size:7px;line-height:.9;margin-left:8px;display:inline-block}
.diff-label{left:131px;top:846px;font-weight:700;font-size:35px;white-space:nowrap}
.diff-box{left:540px;top:852px;width:191px;height:29px;border:1.5px solid #222;background:#fff;font-size:14px;display:flex;align-items:center;justify-content:center}
.certified{left:0;width:856px;top:884px;text-align:center;font-weight:700;font-size:35px;white-space:nowrap}
.footer-panel{left:0;top:936px}
.picture-pill{left:0;top:951px;width:400px;height:51px;background:#fafafa;border-radius:0 26px 26px 0;display:flex;align-items:center;padding-left:26px;font-style:italic;font-size:20px;letter-spacing:2.2px}
.thumb{width:104px;height:105px;border:4px solid #fff;border-radius:14px;background:linear-gradient(180deg,#6c7aa6 0%,#b59a80 45%,#a67b52 70%,#9a928a 100%)}
.logo-tile{left:304px;top:1016px;width:104px;height:105px;background:#fff;border-radius:12px;display:flex;align-items:center;justify-content:center}
.logo-tile .brand{font-size:21px;gap:4px}
.logo-tile .brand-mark{width:13px;height:13px}
.follow{left:95px;top:1128px;color:#fff;font-size:18px;display:flex;align-items:center;gap:8px}
.social{width:26px;height:26px;border:2px solid #fff;border-radius:50%}
.contact-pill{left:498px;top:954px;width:358px;height:50px;background:var(--orange);border-radius:25px 0 0 25px;color:#fff;font-weight:700;font-size:19px;display:flex;align-items:center;padding-left:19px;white-space:nowrap}
.contact-row{left:508px;display:flex;align-items:center;gap:15px;font-size:19px;color:#333;white-space:nowrap}
.contact-row b{font-weight:700;color:#222}
.icon{width:27px;height:27px;border-radius:50%;border:1.5px solid #333;background:#eee;display:flex;align-items:center;justify-content:center}
.bottom-strip{left:0;top:1171px;width:856px;height:29px;background:var(--orange-deep)}
</style>
</head>
<body>
<div class="flyer">
  <div class="abs hero-photo" role="img" aria-label="Photo of the listed stucco home with tile roof under a dusk sky"></div>

  <svg class="abs header-swoosh" width="856" height="160" viewBox="0 0 856 160">
    <path d="M0 0H530C470 90 360 140 200 144C110 146 40 120 0 100Z" fill="#9a9a9a"/>
    <path d="M0 0H530C480 80 380 132 230 138C120 142 50 118 12 96L12 0Z" fill="var(--orange)"/>
    <path d="M12 0H500C450 80 350 126 210 130C120 132 55 112 12 92Z" fill="#fff"/>
  </svg>
  <div class="abs brand brand-top"><span class="brand-mark"></span>Keyvale</div>

  <svg class="abs hero-curve" width="856" height="500" viewBox="0 0 856 500">
    <path d="M0 425C250 470 560 470 856 430V500H0Z" fill="#fbfbfb"/>
    <path d="M0 425C260 462 560 464 856 430V448C560 478 260 482 0 445Z" fill="#cfcfcf" opacity=".8"/>
  </svg>

  <div class="abs purchase-label">PURCHASE&nbsp; PRICE :</div>
  <div class="abs purchase-box"></div>

  <div class="abs section-band band-current">CURRENT MORTGAGE :</div>
  <div class="abs section-band band-new">New Mortgage 10% Down Payment</div>

  <div class="abs label" style="left:27px;top:624px">Loan ammount</div>
  <div class="abs label" style="left:27px;top:651px">Interest rate</div>
  <div class="abs label" style="left:27px;top:678px">Principal 3 interest</div>
  <div class="abs label" style="left:27px;top:705px">Mortgage Insurance</div>
  <div class="abs label" style="left:27px;top:732px">Total</div>
  <div class="abs colon" style="left:225px;top:622px">:</div>
  <div class="abs colon" style="left:225px;top:649px">:</div>
  <div class="abs colon" style="left:225px;top:676px">:</div>
  <div class="abs colon" style="left:225px;top:703px">:</div>
  <div class="abs colon" style="left:225px;top:730px">:</div>
  <div class="abs field" style="left:243px;top:621px;width:115px">Allow Input</div>
  <div class="abs field" style="left:243px;top:648px;width:115px">Allow Input</div>
  <div class="abs field" style="left:243px;top:675px;width:115px">Allow Input</div>
  <div class="abs field" style="left:243px;top:702px;width:115px">Allow Input</div>
  <div class="abs field" style="left:243px;top:729px;width:115px"></div>
  <div class="abs label" style="left:27px;top:759px">Years</div>
  <div class="abs field" style="left:88px;top:757px;width:58px"></div>
  <div class="abs label" style="left:154px;top:759px">Months</div>
  <div class="abs field" style="left:243px;top:757px;width:58px"></div>
  <div class="abs label" style="left:27px;top:790px">Delta</div>
  <div class="abs field" style="left:88px;top:787px;width:267px">Purchase price minus lean amount</div>

  <div class="abs label" style="left:417px;top:630px">Loan ammount</div>
  <div class="abs label" style="left:417px;top:657px">Interest rate</div>
  <div class="abs label" style="left:417px;top:684px">Principal 3 interest</div>
  <div class="abs label" style="left:417px;top:712px">Mortgage Insurance</div>
  <div class="abs label" style="left:417px;top:739px">Total</div>
  <div class="abs colon" style="left:615px;top:628px">:</div>
  <div class="abs colon" style="left:615px;top:655px">:</div>
  <div class="abs colon" style="left:615px;top:682px">:</div>
  <div class="abs colon" style="left:615px;top:710px">:</div>
  <div class="abs colon" style="left:615px;top:737px">:</div>
  <div class="abs field" style="left:633px;top:628px;width:194px;padding-left:15px">90% of purchase price</div>
  <div class="abs field" style="left:633px;top:655px;width:194px;padding-left:15px">Input</div>
  <div class="abs field" style="left:633px;top:682px;width:194px;padding-left:15px">Calc payment</div>
  <div class="abs field" style="left:633px;top:709px;width:194px;padding-left:15px">Input %</div>
  <div class="abs field" style="left:633px;top:736px;width:194px;padding-left:15px">Principal interest +<small>Mortgage<br>Insurance</small></div>
  <div class="abs label" style="left:417px;top:767px">Term</div>
  <div class="abs field center" style="left:477px;top:764px;width:58px">Input</div>
  <div class="abs label" style="left:543px;top:768px">Years</div>
  <div class="abs label" style="left:417px;top:796px">Down payment amount</div>
  <div class="abs field" style="left:663px;top:793px;width:58px"></div>

  <div class="abs diff-label">PAYMENT DIFFERENCE :</div>
  <div class="abs diff-box">Difference Between totals</div>
  <div class="abs certified">This property is “Rate Keeper Approved”</div>

  <svg class="abs footer-panel" width="856" height="236" viewBox="0 0 856 236">
    <path d="M420 0H856V236H405C418 160 418 80 420 0Z" fill="#e6e6e6"/>
    <path d="M0 0H416C410 80 410 160 400 236H0Z" fill="var(--orange)"/>
    <path d="M416 0H424C418 80 416 160 408 236H400C410 160 410 80 416 0Z" fill="#fff"/>
  </svg>
  <div class="abs picture-pill">Picture New Mortgage</div>
  <div class="abs thumb" style="left:32px;top:1016px" role="img" aria-label="Loan officer or home photo slot"></div>
  <div class="abs thumb" style="left:168px;top:1016px" role="img" aria-label="Agent or home photo slot"></div>
  <div class="abs logo-tile"><div class="brand"><span class="brand-mark"></span>Keyvale</div></div>
  <div class="abs follow">Follow us on :<span class="social" style="margin-left:8px"></span><span class="social"></span></div>

  <div class="abs contact-pill">For a FREE Quote Please Contact Us:</div>
  <div class="abs contact-row" style="top:1013px">
    <span class="icon"><svg width="14" height="14" viewBox="0 0 24 24"><path d="M6 2l4 5-2 3c1 3 3 5 6 6l3-2 5 4-3 4C10 22 2 14 2 5Z" fill="#333"/></svg></span>
    <span>OFFICE&nbsp; : <b>0123456789</b></span>
  </div>
  <div class="abs contact-row" style="top:1050px">
    <span class="icon"><svg width="14" height="14" viewBox="0 0 24 24"><path d="M6 2l4 5-2 3c1 3 3 5 6 6l3-2 5 4-3 4C10 22 2 14 2 5Z" fill="#333"/></svg></span>
    <span>MOBILE : <b>0123456789</b></span>
  </div>
  <div class="abs contact-row" style="top:1089px">
    <span class="icon"><svg width="16" height="16" viewBox="0 0 24 24" fill="none" stroke="#333" stroke-width="2"><circle cx="12" cy="12" r="10"/><path d="M2 12h20M12 2c3 3 3 17 0 20M12 2c-3 3-3 17 0 20"/></svg></span>
    <span>www.<b>yourwebsite</b>.com</span>
  </div>
  <div class="abs contact-row" style="top:1127px">
    <span class="icon"><svg width="14" height="14" viewBox="0 0 24 24"><path d="M2 10l10-7 10 7v11H2Z" fill="#333"/></svg></span>
    <span>youremailhere@homemail.com</span>
  </div>

  <div class="abs bottom-strip"></div>
</div>
</body>
</html>
```